Elevating our current Business Card Design

We want to elevate our current business card with a new design to look like a zenith 300 company. We are a premium lubricant distributor (oil and grease).
We need 2 versions, version 1 is as per the uploaded a copy of our current business card with the English version.
For our Chinese version we need to use the front to be English in English and have the back of the card designed exactly like the front for all info to be in Chinese.
The design template needs to be such that we can amend the template with adding different information for each person's card.
The background colour of the card can be changed- we just need to clearly see all information on the card and logos.
The QJR and Ember steady logos cannot have any colour or display changes- only use the logos attached.
All logos need to be included and all information from the attached current card

```html
<!DOCTYPE html>
<html lang="en">
<head>
<meta charset="utf-8">
<title>Vantor Business Card</title>
<link rel="stylesheet" href="https://fonts.googleapis.com/css2?family=Open+Sans:wght@400;600;700;800&display=swap">
<style>
  :root {
    --backdrop: #232323;
    --card-white: #ffffff;
    --brand-red: #e42b25;
    --brand-red-dark: #b51c22;
    --brand-gold: #d49e2a;
    --brand-gold-light: #e7bd3c;
    --ink: #1d1d1d;
    --steel: #9a9ca0;
    --badge-orange: #f07a23;
    --ember-green: #1f4d2e;
  }
  * { box-sizing: border-box; margin: 0; padding: 0; }
  html, body {
    width: 1200px; height: 780px; overflow: hidden;
    background: var(--backdrop);
    font-family: "Open Sans", Arial, sans-serif;
  }
  .canvas {
    position: relative; width: 1200px; height: 780px;
    display: flex; align-items: center; justify-content: center; gap: 40px;
  }
  .card { position: relative; width: 560px; height: 320px; overflow: hidden; }

  /* Back of card */
  .card--back { background: var(--brand-gold); }
  .card--back .pattern-field {
    position: absolute; inset: 0;
    background: radial-gradient(circle at 40% 40%, var(--brand-gold-light) 0%, var(--brand-gold) 70%);
  }
  .card--back .brand-mark {
    position: absolute; left: 50%; top: 50%; transform: translate(-50%, -50%);
    display: flex; align-items: center; gap: 18px;
  }
  .card--back .mark-dot {
    width: 54px; height: 54px; border-radius: 50%; background: var(--card-white);
  }
  .card--back .brand-name {
    font-weight: 800; font-size: 100px; line-height: 1; color: var(--brand-red);
    letter-spacing: -2px;
  }

  /* Front of card */
  .card--front { background: var(--card-white); }
  .card--front .brand-mark {
    position: absolute; right: 26px; top: 22px;
    display: flex; align-items: center; gap: 12px;
  }
  .card--front .mark-dot { width: 32px; height: 32px; border-radius: 50%; background: var(--brand-gold); }
  .card--front .brand-name {
    font-weight: 800; font-size: 60px; line-height: 1; color: var(--brand-red);
    letter-spacing: -1px;
  }

  .contact-rail {
    position: absolute; left: 40px; top: 100px; width: 2px; height: 212px;
    background: var(--brand-red-dark);
  }
  .diamond {
    position: absolute; width: 16px; height: 16px;
    background: var(--brand-red-dark); transform: rotate(45deg);
    display: flex; align-items: center; justify-content: center;
  }
  .diamond svg { transform: rotate(-45deg); width: 10px; height: 10px; }
  .diamond--person { left: 25px; top: 116px; width: 32px; height: 32px; }
  .diamond--person svg { width: 18px; height: 18px; }

  .identity { position: absolute; left: 72px; top: 104px; }
  .identity .person-name {
    font-weight: 700; font-size: 28px; color: var(--brand-red); line-height: 1.1;
  }
  .identity .person-title {
    font-weight: 600; font-size: 13.5px; color: var(--ink); letter-spacing: 0.3px;
  }

  .contact-list { position: absolute; left: 31px; top: 176px; list-style: none; }
  .contact-list li {
    position: relative; height: 18px; padding-left: 42px;
    font-size: 12.5px; color: var(--ink); line-height: 18px; white-space: nowrap;
  }
  .contact-list .diamond { left: 2px; top: 1px; width: 14px; height: 14px; }
  .contact-list .diamond svg { width: 9px; height: 9px; }

  .address {
    position: absolute; left: 31px; top: 274px; padding-left: 42px;
    font-style: normal; font-size: 12.5px; line-height: 17px; color: var(--ink); white-space: nowrap;
  }
  .address .diamond { left: 2px; top: 10px; width: 14px; height: 14px; }
  .address .diamond svg { width: 9px; height: 9px; }

  .cert-row {
    position: absolute; right: 24px; top: 172px; display: flex; gap: 12px;
  }
  .cert-badge {
    width: 36px; height: 36px; border-radius: 50%;
    background: var(--badge-orange); border: 4px solid var(--steel);
  }

  .ember-member {
    position: absolute; left: 292px; top: 212px;
    display: flex; align-items: center; gap: 6px;
  }
  .ember-member .ember-dot { width: 12px; height: 12px; border-radius: 50%; background: var(--ember-green); }
  .ember-member .ember-name { font-weight: 700; font-size: 12px; color: var(--ember-green); line-height: 1.1; }
  .ember-member .ember-note { display: block; font-size: 6.5px; font-weight: 700; letter-spacing: 0.5px; }

  .distributor-strip {
    position: absolute; right: 20px; bottom: 20px;
    display: flex; height: 44px; border: 2px solid var(--brand-red);
  }
  .distributor-strip .strip-brand {
    display: flex; align-items: center; gap: 6px; padding: 0 8px; background: var(--card-white);
  }
  .strip-brand .mark-dot { width: 10px; height: 10px; border-radius: 50%; background: var(--brand-gold); }
  .strip-brand .strip-name { font-weight: 800; font-size: 16px; color: var(--brand-red); }
  .strip-brand .strip-caption { font-size: 6.5px; line-height: 8px; color: var(--brand-red); text-transform: uppercase; }
  .distributor-strip .strip-supplier {
    background: var(--brand-red); color: var(--card-white);
    padding: 0 10px; display: flex; flex-direction: column; justify-content: center;
  }
  .strip-supplier .supplier-name { font-weight: 800; font-size: 16px; line-height: 1; letter-spacing: 1px; }
  .strip-supplier .supplier-line { font-size: 6.5px; font-weight: 600; letter-spacing: 0.5px; }
</style>
</head>
<body>
<main class="canvas">

  <section class="card card--back" aria-label="Card back">
    <div class="pattern-field" role="img" aria-label="Gold embossed repeating brand pattern"></div>
    <div class="brand-mark">
      <span class="mark-dot"></span>
      <span class="brand-name">VANTOR</span>
    </div>
  </section>

  <section class="card card--front" aria-label="Card front">
    <div class="brand-mark">
      <span class="mark-dot"></span>
      <span class="brand-name">VANTOR</span>
    </div>

    <div class="contact-rail"></div>
    <div class="diamond diamond--person">
      <svg viewBox="0 0 20 20" fill="#fff"><circle cx="10" cy="6" r="4"/><path d="M2 19c0-5 3.5-8 8-8s8 3 8 8z"/></svg>
    </div>

    <div class="identity">
      <h1 class="person-name">Maren Holt</h1>
      <p class="person-title">Administration Executive</p>
    </div>

    <ul class="contact-list">
      <li><span class="diamond"><svg viewBox="0 0 12 12" fill="#fff"><path d="M2 1h2.5l1 3-1.5 1a6 6 0 0 0 3 3l1-1.5 3 1V10a1 1 0 0 1-1 1A9 9 0 0 1 1 2a1 1 0 0 1 1-1z"/></svg></span>1300 472 615</li>
      <li><span class="diamond"><svg viewBox="0 0 12 12" fill="none" stroke="#fff" stroke-width="1.4"><rect x="3.5" y="1" width="5" height="10" rx="1"/></svg></span>+61 455 208 317</li>
      <li><span class="diamond"><svg viewBox="0 0 12 12" fill="#fff"><rect x="1" y="5" width="10" height="6" rx="1"/><rect x="3" y="1" width="6" height="4"/></svg></span>+61 8 9024 6350</li>
      <li><span class="diamond"><svg viewBox="0 0 12 12" fill="none" stroke="#fff" stroke-width="1.2"><circle cx="6" cy="6" r="5"/><path d="M1 6h10M6 1c-3 3-3 7 0 10M6 1c3 3 3 7 0 10"/></svg></span>www.vantordirect.com</li>
      <li><span class="diamond"><svg viewBox="0 0 12 12" fill="none" stroke="#fff" stroke-width="1.3"><rect x="1" y="2.5" width="10" height="7"/><path d="M1 2.5l5 4 5-4"/></svg></span>maren.holt@vantordirect.com</li>
    </ul>

    <address class="address">
      <span class="diamond"><svg viewBox="0 0 12 12" fill="#fff"><path d="M6 0.5a4 4 0 0 1 4 4C10 8 6 11.5 6 11.5S2 8 2 4.5a4 4 0 0 1 4-4z"/><circle cx="6" cy="4.5" r="1.5" fill="#b51c22"/></svg></span>
      48 Depot Parade<br>Harlow, WA 6190
    </address>

    <div class="cert-row" aria-label="Certification badges">
      <span class="cert-badge"></span>
      <span class="cert-badge"></span>
      <span class="cert-badge"></span>
    </div>

    <div class="ember-member">
      <span class="ember-dot"></span>
      <span class="ember-name">Ember steady<span class="ember-note">NETWORK MEMBER</span></span>
    </div>

    <div class="distributor-strip">
      <div class="strip-brand">
        <span class="mark-dot"></span>
        <span class="strip-name">VANTOR</span>
        <span class="strip-caption">Vantor<br>Lubricant<br>Distributors</span>
      </div>
      <div class="strip-supplier">
        <span class="supplier-name">KORVAN</span>
        <span class="supplier-line">PREMIUM LUBRICANTS</span>
      </div>
    </div>
  </section>

</main>
</body>
</html>
```